CFO services graphic design

I own a business consulting firm called Thornfield Advisory and we need a graphic for CFO services in our colours and branding. The attached file "CFO services to be put into Thornfield advisory theme", shows the content for the design. The two other files show the theme and colours for the new design.

```html
<!DOCTYPE html>
<html lang="en">
<head>
<meta charset="utf-8">
<title>Thornfield Advisory – CFO Services</title>
<link href="https://fonts.googleapis.com/css2?family=Poppins:wght@400;500;600;700&display=swap" rel="stylesheet">
<style>
  :root {
    --paper: #ffffff;
    --ink: #231f20;
    --orange: #f7941d;
    --orange-deep: #e07a10;
    --flame: #e8590c;
    --rust: #7a2e0a;
    --sky: #1ea6e8;
    --ocean: #1590c8;
    --azure: #1f7fd0;
    --navy: #0d5a94;
    --midnight: #0d3a66;
  }
  html, body { margin: 0; padding: 0; overflow: hidden; background: var(--paper); }
  .canvas { width: 1200px; height: 949px; display: block; background: var(--paper); }
  .brand-name { font-family: 'Poppins', sans-serif; font-weight: 400; fill: var(--orange); font-size: 50px; letter-spacing: 3px; }
  .hub-title { font-family: 'Poppins', sans-serif; font-weight: 700; fill: #fff; font-size: 38px; text-anchor: middle; }
  .label { font-family: 'Poppins', sans-serif; font-weight: 600; fill: var(--ink); font-size: 20px; }
  .sub { font-family: 'Poppins', sans-serif; font-weight: 400; fill: var(--ink); font-size: 13px; }
  .bullet { fill: var(--orange); }
  .icon { fill: none; stroke: var(--ink); stroke-width: 2.4; stroke-linecap: round; stroke-linejoin: round; }
</style>
</head>
<body>
<svg class="canvas" viewBox="107 85 1277 1010" xmlns="http://www.w3.org/2000/svg">
  <defs>
    <linearGradient id="ring-arc" x1="0" x2="1" y1="0" y2="0">
      <stop offset="0" stop-color="var(--orange)"/>
      <stop offset="0.25" stop-color="var(--flame)"/>
      <stop offset="0.4" stop-color="var(--rust)"/>
      <stop offset="0.55" stop-color="var(--sky)"/>
      <stop offset="0.8" stop-color="var(--azure)"/>
      <stop offset="1" stop-color="var(--midnight)"/>
    </linearGradient>
    <g id="medallion-base">
      <circle r="72" fill="none" stroke-width="1.6" stroke-dasharray="5 4" class="dash"/>
    </g>
  </defs>

  <!-- brand -->
  <g class="brand">
    <circle cx="575" cy="233" r="78" fill="var(--orange)"/>
    <text class="brand-name" x="680" y="225">THORNFIELD</text>
    <text class="brand-name" x="680" y="290">ADVISORY</text>
  </g>

  <!-- connecting arc -->
  <path d="M580 481 A190 190 0 1 0 908 483" fill="none" stroke="url(#ring-arc)" stroke-width="5"/>
  <g class="arc-nodes" fill="#fff" stroke-width="5">
    <circle cx="580" cy="481" r="10" stroke="var(--orange)"/>
    <circle cx="561" cy="592" r="10" stroke="var(--flame)"/>
    <circle cx="604" cy="690" r="10" stroke="var(--rust)"/>
    <circle cx="695" cy="750" r="10" stroke="var(--sky)"/>
    <circle cx="804" cy="748" r="10" stroke="var(--ocean)"/>
    <circle cx="884" cy="693" r="10" stroke="var(--azure)"/>
    <circle cx="932" cy="590" r="10" stroke="var(--navy)"/>
    <circle cx="908" cy="483" r="10" stroke="var(--midnight)"/>
  </g>

  <!-- hub -->
  <g class="hub">
    <circle cx="745" cy="570" r="150" fill="var(--orange-deep)"/>
    <circle cx="745" cy="570" r="137" fill="var(--orange)"/>
    <text class="hub-title" x="745" y="550">CHIEF</text>
    <text class="hub-title" x="745" y="585">FINANCIAL</text>
    <text class="hub-title" x="749" y="620">OFFICER</text>
  </g>

  <!-- medallions -->
  <g class="medallion" transform="translate(492 448)">
    <circle r="72" fill="none" stroke="var(--orange)" stroke-width="1.6" stroke-dasharray="5 4"/>
    <circle r="60" fill="var(--orange)"/><circle r="48" fill="#fbb040"/><circle r="41" fill="#fff"/>
    <path class="icon" d="M-22 -4 L6 -20 L6 16 L-22 4 Z M-14 2 L-10 18 M12 -10 L20 -16 M12 0 L22 0"/>
  </g>
  <g class="medallion" transform="translate(467 609)">
    <circle r="72" fill="none" stroke="var(--flame)" stroke-width="1.6" stroke-dasharray="5 4"/>
    <circle r="60" fill="var(--flame)"/><circle r="48" fill="#f47a2a"/><circle r="41" fill="#fff"/>
    <path class="icon" d="M-18 -24 H8 L14 -18 V14 H-18 Z M-12 -10 H6 M-12 -2 H6 M-12 6 H0 M4 18 L20 24 M2 24 H22"/>
  </g>
  <g class="medallion" transform="translate(528 755)">
    <circle r="72" fill="none" stroke="var(--rust)" stroke-width="1.6" stroke-dasharray="5 4"/>
    <circle r="60" fill="var(--rust)"/><circle r="48" fill="#9c3d10"/><circle r="41" fill="#fff"/>
    <path class="icon" d="M-18 -22 H10 V18 H-18 Z M-12 -10 L-9 -7 L-4 -12 M0 -9 H6 M-12 2 L-9 5 L-4 0 M0 3 H6 M10 6 L20 24 H0 Z M10 12 V17"/>
  </g>
  <g class="medallion" transform="translate(663 840)">
    <circle r="72" fill="none" stroke="var(--sky)" stroke-width="1.6" stroke-dasharray="5 4"/>
    <circle r="60" fill="var(--sky)"/><circle r="48" fill="#4cc0f0"/><circle r="41" fill="#fff"/>
    <path class="icon" d="M-20 -24 H14 V22 H-20 Z M-14 -14 H8 M-14 -6 H8 M-14 2 H0 M-8 8 V20 M12 -2 L22 -12"/>
  </g>
  <g class="medallion" transform="translate(824 840)">
    <circle r="72" fill="none" stroke="var(--ocean)" stroke-width="1.6" stroke-dasharray="5 4"/>
    <circle r="60" fill="var(--ocean)"/><circle r="48" fill="#2aa6dc"/><circle r="41" fill="#fff"/>
    <path class="icon" d="M-24 18 A24 24 0 0 1 24 18 Z M0 18 L12 4 M-14 -16 L-12 -20 L-10 -16 M-2 -22 L0 -26 L2 -22 M10 -16 L12 -20 L14 -16"/>
  </g>
  <g class="medallion" transform="translate(960 755)">
    <circle r="72" fill="none" stroke="var(--azure)" stroke-width="1.6" stroke-dasharray="5 4"/>
    <circle r="60" fill="var(--azure)"/><circle r="48" fill="#3b9be6"/><circle r="41" fill="#fff"/>
    <path class="icon" d="M-20 -4 A14 14 0 1 1 -6 10 M-6 -12 V-4 H0 M-4 -6 H24 V22 H-4 Z M2 4 H8 M12 4 H18 M2 12 H8 M12 12 H18"/>
  </g>
  <g class="medallion" transform="translate(1024 609)">
    <circle r="72" fill="none" stroke="var(--navy)" stroke-width="1.6" stroke-dasharray="5 4"/>
    <circle r="60" fill="var(--navy)"/><circle r="48" fill="#1670b0"/><circle r="41" fill="#fff"/>
    <path class="icon" d="M-22 16 L-6 4 H10 L20 -2 M-14 24 L4 14 H14 L24 6 M0 -18 A7 7 0 1 0 0.1 -18 M14 -4 A6 6 0 1 0 14.1 -4"/>
  </g>
  <g class="medallion" transform="translate(1000 448)">
    <circle r="72" fill="none" stroke="var(--midnight)" stroke-width="1.6" stroke-dasharray="5 4"/>
    <circle r="60" fill="var(--midnight)"/><circle r="48" fill="#164e84"/><circle r="41" fill="#fff"/>
    <path class="icon" d="M-12 -24 H12 V6 M-12 -24 V16 H0 M-4 -8 V-14 M2 -8 V-18 M8 -8 V-12 M10 10 A8 8 0 1 0 10.1 10 M16 16 L24 24 M-22 -2 A6 6 0 1 0 -21.9 -2"/>
  </g>

  <!-- labels -->
  <g class="labels">
    <text class="label" x="234" y="424">Communication:</text>
    <g class="sub">
      <text x="242" y="445">Board of Directors,</text>
      <text x="242" y="459">Creditors,</text>
      <text x="242" y="474">owners,</text>
      <text x="242" y="488">investors,</text>
      <text x="242" y="503">credit rating agencies</text>
    </g>
    <g class="bullet">
      <circle cx="235" cy="440" r="1.8"/><circle cx="235" cy="454" r="1.8"/><circle cx="235" cy="469" r="1.8"/>
      <circle cx="235" cy="483" r="1.8"/><circle cx="235" cy="498" r="1.8"/>
    </g>

    <text class="label" x="232" y="602">Compliance:</text>
    <circle class="bullet" cx="235" cy="613" r="1.8"/>
    <text class="sub" x="244" y="620">Tax, legal and</text>
    <text class="sub" x="244" y="635">regulatory</text>

    <text class="label" x="380" y="784" text-anchor="middle">Risk</text>
    <text class="label" x="382" y="807" text-anchor="middle">Management</text>

    <text class="label" x="624" y="950" text-anchor="middle">Budgeting &amp;</text>
    <text class="label" x="626" y="973" text-anchor="middle">Strategic Planning</text>

    <text class="label" x="858" y="950" text-anchor="middle">Performance</text>
    <text class="label" x="860" y="973" text-anchor="middle">Evaluation</text>

    <text class="label" x="1063" y="764">Long-term</text>
    <text class="label" x="1063" y="787">&amp; short-term</text>
    <text class="label" x="1063" y="810">investment</text>
    <text class="label" x="1063" y="833">decisions</text>

    <text class="label" x="1128" y="589">Captial</text>
    <text class="label" x="1128" y="612">Structure and</text>
    <text class="label" x="1128" y="635">the Cost of</text>
    <text class="label" x="1128" y="658">Capital</text>

    <text class="label" x="1099" y="427">Cost Accounting</text>
    <text class="label" x="1099" y="450">&amp; Cost</text>
    <text class="label" x="1099" y="474">Management</text>
  </g>
</svg>
</body>
</html>
```